Redesign and move to Wordpress for corvandel.com

Our website needs a redesign and at the same time we are moving it to Wordpress. Please help us with a new digital professional look and feel.

We are an Australian Software Engineering company specialising in advanced software development using in A.I., PLatform Engineering, Integration and Cloud. See the current corvandel.com for more information about us.

```html
<!DOCTYPE html>
<html lang="en">
<head>
<meta charset="utf-8">
<title>Corvandel – Book a consultation</title>
<link href="https://fonts.googleapis.com/css2?family=Poppins:wght@400;500;600;700&family=Roboto:wght@400;700&display=swap" rel="stylesheet">
<style>
:root{
  --ink:#111317;
  --muted:#5f6673;
  --faint:#a3a8b2;
  --line:#dfe2e7;
  --cell-off:#f4f5f7;
  --green:#12d087;
  --footer-a:#2a0a5e;
  --footer-b:#14052e;
  --footer-text:#c9c0dc;
  --white:#ffffff;
}
*{box-sizing:border-box;margin:0;padding:0}
html,body{width:875px;height:1200px;overflow:hidden;background:var(--white)}
body{font-family:'Poppins',sans-serif;color:var(--ink)}
.page{position:relative;width:1280px;height:1756px;transform:scale(0.68359);transform-origin:0 0}
.abs{position:absolute}

.intro{left:0;width:1280px;top:64px;text-align:center;font-size:17px}
.portrait{left:537px;top:120px;width:206px;height:206px;border-radius:50%;
  background:radial-gradient(circle at 50% 40%,#8a6a58 0%,#4a4541 45%,#2a2d31 100%)}
.title{left:0;width:1280px;top:350px;text-align:center;font-size:25px;font-weight:600}

.steps{left:110px;top:480px;width:220px;height:245px;border:1px solid var(--line);border-radius:5px;box-shadow:0 2px 6px rgba(0,0,0,.04)}
.step{position:absolute;left:21px;display:flex;align-items:center;gap:12px;font-size:14px;color:#3b414b}
.step-icon{width:32px;height:32px;border:1px solid var(--line);border-radius:5px;display:flex;align-items:center;justify-content:center}
.step.active{color:var(--green)}
.step.active .step-icon{background:var(--green);border-color:var(--green)}

.booking{left:362px;top:480px;width:808px;height:677px;border:1px solid var(--line);border-radius:4px;overflow:hidden}
.viewport{position:absolute;left:0;top:0;width:806px;height:600px;overflow:hidden}
.scrollbar{position:absolute;right:0;top:0;width:16px;height:600px;background:#f1f1f1}
.thumb{position:absolute;left:2px;top:75px;width:12px;height:353px;background:#c1c1c1}
.arrow-up,.arrow-down{position:absolute;left:5px;width:0;height:0;border-left:3px solid transparent;border-right:3px solid transparent}
.arrow-up{top:7px;border-bottom:4px solid #505050}
.arrow-down{bottom:7px;border-top:4px solid #505050}

.calendar{position:absolute;left:24px;top:9px;width:741px;border:1px solid var(--line);display:grid;grid-template-columns:repeat(7,1fr)}
.dow{height:40px;display:flex;align-items:center;justify-content:center;font-size:14px;color:#3b414b;border-bottom:1px solid var(--line)}
.day{height:56.5px;display:flex;align-items:center;justify-content:center;font-size:13px;color:var(--faint);background:var(--cell-off);border-right:1px solid var(--line);border-bottom:1px solid var(--line)}
.day:nth-child(7n){border-right:none}
.day.open{background:var(--white);color:#2c313a}
.day.selected{background:var(--green);color:var(--white)}
.calendar .day:nth-last-child(-n+7){border-bottom:none}

.slots{position:absolute;left:24px;top:412px;width:741px;height:220px;border:1px solid var(--line);padding:26px 20px}
.slots h3{font-size:18px;font-weight:600;color:#1c2028}
.slots h4{font-size:16px;font-weight:400;color:var(--muted);margin-top:8px}
.slot-grid{display:grid;grid-template-columns:1fr 1fr;gap:9px 9px;margin-top:12px;width:691px}
.slot{height:34px;border:1px solid var(--line);border-radius:3px;font-size:13px;color:#3b414b;display:flex;align-items:center;padding-left:11px}

.actions{position:absolute;left:0;top:600px;width:808px;height:77px;border-top:1px solid var(--line);background:var(--white)}
.back{position:absolute;left:465px;top:28px;font-size:14px;color:#3b414b;display:flex;align-items:center;gap:5px}
.next{position:absolute;left:582px;top:17px;width:196px;height:42px;background:var(--green);border-radius:3px;color:var(--white);font-size:14px;font-weight:600;display:flex;align-items:center;justify-content:center;gap:6px}

.footer{left:0;top:1310px;width:1280px;height:446px;background:radial-gradient(ellipse at 20% 60%,#35107a 0%,var(--footer-a) 35%,var(--footer-b) 75%),var(--footer-b);color:var(--white)}
.footer::after{content:"";position:absolute;right:0;top:0;width:420px;height:446px;background:radial-gradient(ellipse at 80% 60%,rgba(120,90,140,.35),transparent 70%)}
.brand{position:absolute;left:60px;top:90px;display:flex;align-items:center;gap:20px}
.brand-mark{width:56px;height:56px;border:3px solid var(--white)}
.brand-name{font-size:40px;font-weight:400;letter-spacing:2px;color:var(--white)}
.mission{position:absolute;left:60px;top:170px;width:322px;font-family:'Roboto',sans-serif;font-size:14.5px;line-height:21px;color:var(--footer-text)}
.mission b{color:var(--footer-text)}
.col{position:absolute;top:102px;z-index:1}
.col h5{font-size:23px;font-weight:400;margin-bottom:18px}
.col a{display:block;font-size:12px;font-weight:600;color:var(--white);text-decoration:none;letter-spacing:.2px;height:34.5px;line-height:18px}
.contact p{font-size:14px;line-height:26px;color:var(--white)}
.contact p+p{margin-top:14px}
.divider{position:absolute;left:0;top:362px;width:1280px;height:1px;background:rgba(255,255,255,.12)}
.copyright{position:absolute;left:50px;top:384px;font-family:'Roboto',sans-serif;font-size:16px;color:var(--footer-text)}
.social{position:absolute;top:394px;width:14px;height:14px;border-radius:50%;background:var(--white);z-index:1}
</style>
</head>
<body>
<div class="page">
  <p class="abs intro">Book an obligation free consultation with our Lead Technologist</p>
  <div class="abs portrait" role="img" aria-label="Portrait photo of the Lead Technologist"></div>
  <h1 class="abs title">Meet with our CTO</h1>

  <nav class="abs steps">
    <div class="step" style="top:24px"><span class="step-icon"><svg width="14" height="12" viewBox="0 0 14 12"><rect x="1" y="1" width="12" height="4" rx="1" fill="#5f6673"/><rect x="1" y="7" width="12" height="4" rx="1" fill="#5f6673"/></svg></span>Service</div>
    <div class="step active" style="top:78px"><span class="step-icon"><svg width="13" height="13" viewBox="0 0 13 13"><rect x="1" y="2" width="11" height="10" rx="1" fill="none" stroke="#fff" stroke-width="1.5"/><line x1="1" y1="5" x2="12" y2="5" stroke="#fff" stroke-width="1.5"/></svg></span>Date &amp; Time</div>
    <div class="step" style="top:132px"><span class="step-icon"><svg width="12" height="13" viewBox="0 0 12 13"><rect x="1" y="1" width="10" height="11" rx="1" fill="#5f6673"/><line x1="3.5" y1="5" x2="8.5" y2="5" stroke="#fff"/><line x1="3.5" y1="8" x2="8.5" y2="8" stroke="#fff"/></svg></span>Basic Details</div>
    <div class="step" style="top:186px"><span class="step-icon"><svg width="12" height="13" viewBox="0 0 12 13"><rect x="1" y="1" width="10" height="11" rx="1" fill="#5f6673"/><path d="M3.5 6.5l2 2 3-4" stroke="#fff" stroke-width="1.3" fill="none"/></svg></span>Summary</div>
  </nav>

  <section class="abs booking">
    <div class="viewport">
      <div class="calendar">
        <div class="dow">Mon</div><div class="dow">Tue</div><div class="dow">Wed</div><div class="dow">Thu</div><div class="dow">Fri</div><div class="dow">Sat</div><div class="dow">Sun</div>
        <div class="day">30</div><div class="day">31</div><div class="day">1</div><div class="day">2</div><div class="day">3</div><div class="day">4</div><div class="day">5</div>
        <div class="day">6</div><div class="day">7</div><div class="day">8</div><div class="day">9</div><div class="day">10</div><div class="day">11</div><div class="day">12</div>
        <div class="day">13</div><div class="day">14</div><div class="day">15</div><div class="day">16</div><div class="day">17</div><div class="day">18</div><div class="day">19</div>
        <div class="day">20</div><div class="day">21</div><div class="day">22</div><div class="day selected">23</div><div class="day open">24</div><div class="day">25</div><div class="day">26</div>
        <div class="day">27</div><div class="day">28</div><div class="day open">29</div><div class="day open">30</div><div class="day open">31</div><div class="day">1</div><div class="day">2</div>
        <div class="day">3</div><div class="day">4</div><div class="day">5</div><div class="day">6</div><div class="day">7</div><div class="day">8</div><div class="day">9</div>
      </div>

      <div class="slots">
        <h3>Time Slot</h3>
        <h4>Morning</h4>
        <div class="slot-grid">
          <div class="slot">03:00 am to 03:30 am</div>
          <div class="slot">03:30 am to 04:00 am</div>
          <div class="slot">04:00 am to 04:30 am</div>
          <div class="slot">04:30 am to 05:00 am</div>
        </div>
      </div>

      <div class="scrollbar"><span class="arrow-up"></span><span class="thumb"></span><span class="arrow-down"></span></div>
    </div>

    <div class="actions">
      <div class="back"><svg width="18" height="10" viewBox="0 0 18 10"><path d="M17 5H2M5.5 1.5L2 5l3.5 3.5" stroke="#3b414b" stroke-width="1.4" fill="none"/></svg>Go Back</div>
      <div class="next">Next: Basic Details <svg width="18" height="10" viewBox="0 0 18 10"><path d="M1 5h15M12.5 1.5L16 5l-3.5 3.5" stroke="#fff" stroke-width="1.4" fill="none"/></svg></div>
    </div>
  </section>

  <footer class="abs footer">
    <div class="brand"><span class="brand-mark"></span><span class="brand-name">corvandel</span></div>
    <p class="mission">We have been on a mission to make <b>complex custom enterprise integration</b> accessible to any organisation, regardless of industry, size, or location.</p>

    <div class="col" style="left:539px">
      <h5>Navigation</h5>
      <a>HOME</a><a>ABOUT</a><a>SERVICES</a><a>WORK</a><a>CONTACT</a>
    </div>
    <div class="col" style="left:793px">
      <h5>Solutions</h5>
      <a>OUR SERVICES</a><a>OUR SERVICES V2</a><a>OUR SERVICES V3</a><a>OUR SERVICES V4</a>
    </div>
    <div class="col contact" style="left:1046px">
      <h5>Contact Us</h5>
      <p>Suite 210, 48 Harlow Street<br>Carlton, VIC , 3053</p>
      <p>1800-472-906<br>info@corvandel.com</p>
    </div>

    <div class="divider"></div>
    <p class="copyright">© 2013 . All rights reserved Corvandel</p>
    <span class="social" style="left:1149px" aria-label="Social link"></span>
    <span class="social" style="left:1184px" aria-label="Social link"></span>
    <span class="social" style="left:1221px" aria-label="Social link"></span>
  </footer>
</div>
</body>
</html>
```